Business Card Design

We need a business card designed for our new company. Prefer a black card with white logo & writing.

Contact Information for Business Card

Ted Galloway, address: 7-4812 Fernhollow Road, Abbotsford, BC, V3K 8R2, Office Phone: 604-712-3390, Cell: 604-947-2164, Email: ted@resinworkshub.ca

Colors

Designer to choose only greyscale colors for use in the design.

```html
<!DOCTYPE html>
<html lang="en">
<head>
<meta charset="utf-8">
<title>Resinworks Hub — Business Card</title>
<link href="https://fonts.googleapis.com/css2?family=Poppins:wght@300;400;600;700&display=swap" rel="stylesheet">
<style>
  :root {
    --backdrop: #1e1e1f;
    --card: #222224;
    --card-edge: #3a3a3c;
    --ink: #ffffff;
    --ink-soft: #d9d9d9;
    --steel-light: #bdbdbd;
    --steel-dark: #2a2a2c;
  }
  * { margin: 0; padding: 0; box-sizing: border-box; }
  html, body {
    width: 1200px; height: 711px; overflow: hidden;
    background: var(--backdrop);
    font-family: "Poppins", sans-serif;
    color: var(--ink);
  }
  .stage {
    width: 1200px; height: 711px;
    display: flex; align-items: center; justify-content: center; gap: 48px;
  }
  .card {
    position: relative;
    width: 540px; height: 309px;
    background: var(--card);
    border: 1px solid var(--card-edge);
    border-radius: 3px;
    box-shadow: 0 18px 40px rgba(0,0,0,.55);
    overflow: hidden;
  }
  /* front */
  .card--front { display: flex; align-items: center; justify-content: center; }
  .brand { display: flex; align-items: center; gap: 12px; }
  .brand__mark { width: 18px; height: 18px; border: 2px solid currentColor; }
  .brand__name {
    font-weight: 700; letter-spacing: .04em; text-transform: uppercase; line-height: 1;
  }
  .card--front .brand { color: #3c3c3e; }
  .card--front .brand__name { font-size: 40px; }
  .card--front .brand__mark { width: 30px; height: 30px; border-width: 3px; }

  /* back */
  .name-block {
    position: absolute; top: 34px; right: 30px; text-align: right;
  }
  .name-block__name { font-size: 30px; line-height: 1; font-weight: 300; }
  .name-block__name strong { font-weight: 700; }
  .name-block__title { font-size: 13px; font-weight: 400; margin-top: 4px; }
  .name-bar {
    position: absolute; top: 30px; right: 0; width: 14px; height: 58px; background: var(--ink);
  }
  .card--back .brand { position: absolute; top: 108px; left: 34px; color: var(--ink); }
  .card--back .brand__name { font-size: 26px; }
  .contact {
    position: absolute; left: 34px; bottom: 26px;
    font-size: 12.5px; font-weight: 300; color: var(--ink-soft); line-height: 1.45;
  }
  .contact__address { margin-bottom: 10px; }
  .contact__list { list-style: none; }
  .contact__list li { display: flex; align-items: center; gap: 10px; }
  .contact__list svg { width: 12px; height: 12px; flex: none; }
  .ridge {
    position: absolute; right: 0; bottom: 0; width: 260px; height: 180px;
    background: linear-gradient(160deg, var(--steel-light) 0%, #6d6d6f 25%, var(--steel-dark) 70%);
    clip-path: polygon(30% 0, 100% 8%, 100% 100%, 0 100%);
    opacity: .55;
  }
</style>
</head>
<body>
<main class="stage">
  <section class="card card--front" aria-label="Card front">
    <div class="brand">
      <span class="brand__mark"></span>
      <span class="brand__name">Resinworks Hub</span>
    </div>
  </section>

  <section class="card card--back" aria-label="Card back">
    <div class="ridge" role="img" aria-label="Silver mountain ridge illustration"></div>
    <div class="name-bar"></div>
    <div class="name-block">
      <p class="name-block__name"><strong>Ted</strong> Galloway</p>
      <p class="name-block__title">Founder &amp; CEO</p>
    </div>
    <div class="brand">
      <span class="brand__mark"></span>
      <span class="brand__name">Resinworks Hub</span>
    </div>
    <div class="contact">
      <p class="contact__address">7-4812 Fernhollow Road,<br>Abbotsford, BC, V3K 8R2.</p>
      <ul class="contact__list">
        <li>
          <svg viewBox="0 0 24 24" fill="#fff"><path d="M6.6 10.8a15 15 0 0 0 6.6 6.6l2.2-2.2c.3-.3.7-.4 1-.2 1.1.4 2.3.6 3.6.6.6 0 1 .4 1 1V20c0 .6-.4 1-1 1A17 17 0 0 1 3 4c0-.6.4-1 1-1h3.5c.6 0 1 .4 1 1 0 1.3.2 2.5.6 3.6.1.3 0 .7-.2 1z"/></svg>
          604-712-3390
        </li>
        <li>
          <svg viewBox="0 0 24 24" fill="none" stroke="#fff" stroke-width="2"><rect x="6" y="2" width="12" height="20" rx="2"/><line x1="11" y1="18" x2="13" y2="18"/></svg>
          604-947-2164
        </li>
        <li>
          <svg viewBox="0 0 24 24" fill="none" stroke="#fff" stroke-width="2"><circle cx="12" cy="12" r="10"/><path d="M2 12h20M12 2a15 15 0 0 1 0 20M12 2a15 15 0 0 0 0 20"/></svg>
          www.resinworkshub.ca
        </li>
        <li>
          <svg viewBox="0 0 24 24" fill="none" stroke="#fff" stroke-width="2"><rect x="2" y="5" width="20" height="14" rx="1"/><path d="M2 6l10 7 10-7"/></svg>
          ted@resinworkshub.ca
        </li>
      </ul>
    </div>
  </section>
</main>
</body>
</html>
```